BRTL web site redesign

Coastal Linkage Engineering service (BRTL) is a diverse technology company specialising in design and installation of fibre optics, network convergence and building services, for commercial clients in Australia, we required a new design of our website to attract new clients, generate sales leads, and provide information about our services to the market. The site and should have a new technology look and feel and be designed in word press. our branding colour is blue.

Target Market(s)

New developments, Construction organisations, Commercial end users, IT managers, Consultants.

Industry/Entity Type

It Company

Number of Pages Required

5+ page

Font styles to use
Sans Serif

Colors
0292cd
3176b5

Requirements
Must have
• key pages.
• Home page with some sizzle, automated pictures running through, I like the look of this competitor website http://www.gleamwirex.com.au/ good clean menus and easy to navigate.
• Services page our key services are Fibre optics, Security, Building services,Electrical. I would like the same page layout (Design) for all our services, with a find out more link on each page, manly picture driven with text around our key messaging.
• About us page with space for company profile and directors pictures, bio and contact information.
• Certifications / Accreditations page with have over 20 certifications on different products from suppliers, and a number of licences from governing bodies.
• Current and past projects page with case studies and customer outcomes
• Contact us page with options around what services they require more information on, please keep in mind the site is around generating sales Leeds and being seen as an industry expert.
Nice to have
• RSS feeds, Linked in link, to be placed within the design, Consistent BRTL branding,Same colour blue as our logo Document library for education information, white papers, presentations etc,
• a new technology look and feel, mobile friendly.
Should not have
• boring layout, move away from our cuurent website http://www.brtlgroup.com.au/
• no e eCommerce store required.

```html
<!DOCTYPE html>
<html lang="en">
<head>
<meta charset="utf-8">
<title>BRTL – Communications Integration</title>
<link href="https://fonts.googleapis.com/css2?family=Lato:wght@400;700&family=Old+Standard+TT:wght@400;700&display=swap" rel="stylesheet">
<style>
:root{
  --page-bg:#e9f0f5;
  --topbar:#2a2a2a;
  --brand:#0a85bf;
  --brand-deep:#0672a6;
  --brand-light:#d6ecf7;
  --heading:#0c79b3;
  --text:#333;
  --footer:#231f20;
  --footer-line:#3d3839;
  --white:#fff;
}
*{box-sizing:border-box;margin:0;padding:0}
html,body{width:1200px;height:2345px;overflow:hidden}
body{background:var(--page-bg);font-family:'Lato',sans-serif;color:var(--text);position:relative}
.serif{font-family:'Old Standard TT',serif}

/* top bar */
.topbar{position:absolute;left:124px;top:0;width:952px;height:34px;background:var(--topbar);color:#eee;font-size:11px;display:flex;align-items:center;padding:0 18px}
.topbar .welcome{flex:1}
.topbar .social{position:absolute;left:568px;top:11px;display:flex;gap:10px}
.topbar .social span{width:12px;height:12px;border-radius:50%;background:#ddd;display:block}
.topbar .links{display:flex;gap:26px;align-items:center}
.topbar .links span{display:flex;align-items:center;gap:5px}

/* header */
.header{position:absolute;left:124px;top:34px;width:952px;height:128px;background:var(--brand)}
.logo{position:absolute;left:17px;top:13px;width:196px;height:99px;color:var(--white);font-weight:700}
.logo .name{font-size:58px;letter-spacing:2px;line-height:70px;display:flex;align-items:center;gap:10px}
.logo .name i{width:22px;height:22px;background:var(--white);display:block}
.logo .sub{font-size:7.5px;letter-spacing:.2px;text-transform:uppercase}
.nav{position:absolute;left:247px;top:35px;width:689px;height:57px;background:linear-gradient(#fff,#dcedf7);border-radius:4px;display:flex;align-items:center;padding-left:18px;font-size:13.5px;color:var(--brand-deep)}
.nav a{padding:0 17px;height:100%;display:flex;align-items:center;color:inherit;text-decoration:none}
.nav a.active{background:#cfe6f3;margin-top:0}
.dropdown{position:absolute;left:525px;top:126px;width:169px;height:114px;background:var(--brand-light);font-size:13px;color:var(--brand-deep);z-index:3;padding-top:10px}
.dropdown div{height:36px;display:flex;align-items:center;padding:0 19px;justify-content:space-between}
.dropdown div.on{background:linear-gradient(#fff,#cde4f1);margin:0 14px 0 10px;padding-left:9px;height:26px;border:1px solid #b8d6e8}

/* hero */
.hero{position:absolute;left:124px;top:162px;width:952px;height:446px;background:linear-gradient(120deg,#35606d 0%,#5a7a82 30%,#2d3a40 55%,#6f8a93 80%,#3d5c72 100%)}
.hero-shadow{position:absolute;left:300px;top:608px;width:600px;height:30px;background:radial-gradient(ellipse at top,rgba(0,0,0,.25),transparent 70%)}
.caption{position:absolute;left:184px;top:294px;width:553px;height:133px;background:rgba(0,0,0,.72);color:var(--white);padding:24px 26px}
.caption h1{font-size:21px;font-weight:400;margin-bottom:12px}
.caption p{font-size:14px;line-height:18px}
.btn{display:flex;align-items:center;justify-content:center;background:linear-gradient(#fff,#cfe6f3);color:var(--brand-deep);font-size:13px;font-weight:700;border-radius:3px;position:absolute}
.btn.read{left:184px;top:438px;width:138px;height:38px}
.arrow{position:absolute;top:363px;width:55px;height:45px;background:var(--brand)}
.arrow.left{left:97px}.arrow.right{left:1048px}

/* section headings */
.sec-title{position:absolute;left:0;width:1200px;text-align:center;font-size:34px;color:var(--heading);font-weight:700}
.sec-title span{position:relative;padding:0 18px}
.sec-title span::before,.sec-title span::after{content:"";position:absolute;top:50%;width:88px;height:1px;background:currentColor}
.sec-title span::before{right:100%}.sec-title span::after{left:100%}
.sec-title.light{color:var(--white)}

/* about */
.about-img{position:absolute;left:124px;top:734px;width:300px;height:243px;background:radial-gradient(circle at 50% 45%,#cdf3ff 0%,#2aa8e0 30%,#0a3d8a 75%,#061c4a 100%)}
.about-text{position:absolute;left:451px;top:732px;width:625px;font-size:12.3px;line-height:16px;color:#222}
.about-text p{margin-bottom:16px}
.btn-blue{position:absolute;left:451px;top:943px;width:137px;height:34px;background:linear-gradient(#5cc8f4,#0a93cf);color:var(--white);font-size:11px;border-radius:3px;display:flex;align-items:center;justify-content:center}

/* services */
.services{position:absolute;left:124px;top:1013px;width:952px;height:402px;background:var(--brand)}
.service{position:absolute;top:80px;width:210px;text-align:center;color:var(--white)}
.service .pic{width:184px;height:184px;border-radius:50%;border:2px solid #fff;margin:0 auto;display:flex;align-items:center;justify-content:center}
.service h3{font-weight:400;font-size:21px;margin-top:28px}
.service p{font-size:11px;line-height:13.5px;text-align:justify;margin-top:8px;height:40px;overflow:hidden;padding:0 14px}

/* projects */
.tabs .tab{position:absolute;top:1500px;height:33px;background:linear-gradient(#68c9f2,#1097d1);color:var(--white);font-size:14px;border-radius:3px;display:flex;align-items:center;justify-content:center}
.tab.all::after{content:"";position:absolute;bottom:-8px;left:50%;margin-left:-8px;border:8px solid transparent;border-top-color:#1097d1;border-bottom:0}
.project{position:absolute;top:1568px;width:300px}
.project .pic{height:188px}
.project h4{font-size:15px;font-weight:400;color:var(--heading);margin-top:18px}
.project p{font-size:11.5px;line-height:15px;margin-top:12px;color:#222;height:62px;overflow:hidden}

/* footer */
.footer{position:absolute;left:124px;top:1917px;width:952px;height:428px;background:var(--footer);color:var(--white)}
.footer h5{position:absolute;top:30px;font-size:19px;font-weight:400}
.footer .intro{position:absolute;left:17px;top:72px;font-size:12px}
.field{position:absolute;background:var(--white);color:#777;font-size:11px;padding:6px 6px;border-radius:1px}
.submit{position:absolute;left:17px;top:303px;width:120px;height:34px;background:linear-gradient(#fff,#cfe6f3);color:#222;font-size:11px;font-weight:700;border-radius:3px;display:flex;align-items:center;justify-content:center}
.flist{position:absolute;top:76px;width:140px;font-size:12.5px}
.flist div{height:38px;border-bottom:1px solid var(--footer-line);padding-top:4px}
.tweets{position:absolute;left:735px;top:76px;width:200px}
.tweet{display:flex;gap:8px;height:75px;border-bottom:1px solid var(--footer-line);margin-bottom:1px;padding-top:2px}
.tweet i{width:16px;height:16px;border-radius:50%;background:var(--white);flex:none;margin-top:4px}
.tweet p{font-size:11px;line-height:14px}
.tweet small{display:block;color:#aaa;font-size:10.5px;margin-top:6px;margin-left:-24px}
.footer .rule{position:absolute;left:17px;right:17px;top:364px;height:1px;background:var(--footer-line)}
.copy{position:absolute;left:0;right:0;top:388px;text-align:center;font-size:10.5px;color:#999}
</style>
</head>
<body>

<div class="topbar">
  <div class="welcome">Wel come...!!!</div>
  <div class="social"><span></span><span></span><span></span></div>
  <div class="links">
    <span>&#8964; <svg width="10" height="10" viewBox="0 0 10 10"><circle cx="5" cy="3" r="2.5" fill="#eee"/><path d="M0 10a5 4 0 0 1 10 0z" fill="#eee"/></svg> My Account</span>
    <span>&#8964; <svg width="11" height="10" viewBox="0 0 11 10"><path d="M0 1h2l2 6h6l1-5H3" stroke="#eee" fill="none"/><circle cx="5" cy="9" r="1" fill="#eee"/><circle cx="9" cy="9" r="1" fill="#eee"/></svg> My Cart</span>
    <span><svg width="10" height="10" viewBox="0 0 10 10"><path d="M2 0l2 2-1 2 3 3 2-1 2 2-2 2C4 10 0 6 0 2z" fill="#eee"/></svg> 1300 555 214</span>
  </div>
</div>

<header class="header">
  <div class="logo">
    <div class="name"><i></i>BRTL</div>
    <div class="sub">Coastal Linkage Engineering Service</div>
  </div>
  <nav class="nav">
    <a>Home</a><a>About Us</a><a class="active">Services</a><a>Commercial</a><a>ISP</a><a>Recent Projects</a><a>Contact Us</a><a>Blog</a>
  </nav>
</header>
<div class="dropdown">
  <div>Item 1 <span>&#9656;</span></div>
  <div class="on">Item 2</div>
  <div>Item 3</div>
</div>

<section class="hero" role="img" aria-label="Slideshow photo of a technician splicing fibre optic cables"></section>
<div class="hero-shadow"></div>
<div class="caption">
  <h1 class="serif">BRTL Is A Communications Intergration Company</h1>
  <p>Incorporating The Expertise Of Data And Fibre Optic Communication,<br>ICT And Low Voltage System, Security And Application Services.</p>
</div>
<div class="btn read">READ MORE</div>
<div class="arrow left"><svg width="55" height="45"><path d="M18 22h20M18 22l7-6M18 22l7 6" stroke="#fff" stroke-width="3" fill="none"/></svg></div>
<div class="arrow right"><svg width="55" height="45"><path d="M17 22h20M37 22l-7-6M37 22l-7 6" stroke="#fff" stroke-width="3" fill="none"/></svg></div>

<h2 class="sec-title serif" style="top:666px"><span>&#9670;About Us&#9670;</span></h2>
<div class="about-img" role="img" aria-label="Glowing blue fibre optic strands"></div>
<div class="about-text">
  <p>BRTL is a Communications Integration Company incorporating the expertise of Data and Fibre Optic Communications, ICT and low voltage systems, Security and Application Services. with over five decades of experience and successes in their respected field of expertise. The quality and proven ability of our management and tradespeople, in conjunction with our extensive network of resources, ensures a successful outcome for our clients.</p>
  <p>At BRTL our mission is to maximise the value of the service offered to our clients and perform these services through a well-managed process, focusing on quality, technical reliability and cost effectiveness.It is our commitment to provide service with the highest professional standard of excellence, integrity and efficiency.</p>
  <p>BRTL is able to provide a unique level of knowledge and experience to address the issues associated with all projects. We have extensive experience in many types of installations across a wide variety of environments, which provides us with skills in identifying problems early providing resolutions, which allows us to deliver a successful outcome.</p>
</div>
<div class="btn-blue">LEARN MORE</div>

<section class="services">
  <h2 class="sec-title light serif" style="top:22px;left:-124px"><span>&#9670;Our Services&#9670;</span></h2>
  <div class="service" style="left:5px">
    <div class="pic" role="img" aria-label="Blue fibre optic light burst" style="background:radial-gradient(circle,#8fe0ff,#1a8fd0 60%,#0a4f9a)">
      <svg width="38" height="38"><circle cx="19" cy="19" r="19" fill="#fff"/><circle cx="17" cy="17" r="6" stroke="#0a85bf" stroke-width="2.5" fill="none"/><path d="M21 21l6 6" stroke="#0a85bf" stroke-width="3"/></svg>
    </div>
    <h3>Fibre Optics</h3>
    <p>BRTL has highly trained and proficient engineers, technicians and project managers to ensure that we deliver every fibre project on time.</p>
  </div>
  <div class="service" style="left:249px">
    <div class="pic" role="img" aria-label="Security camera on an office tower" style="background:linear-gradient(160deg,#cfdde8,#7e9db5 60%,#4a6580)"></div>
    <h3>Security</h3>
    <p>The BRTL range of IP CCTV cameras and platforms allows you to keep current with technology advances in site security.</p>
  </div>
  <div class="service" style="left:492px">
    <div class="pic" role="img" aria-label="Two workers on a rooftop above a city" style="background:linear-gradient(170deg,#9fb3c4,#5f7083 55%,#3a3f46)"></div>
    <h3>Building Services</h3>
    <p>BRTL has highly trained and proficient engineers, technicians and project managers to ensure that we meet every building need.</p>
  </div>
  <div class="service" style="left:737px">
    <div class="pic" role="img" aria-label="Orange electrical switchboard panels" style="background:linear-gradient(150deg,#f08a3a,#d2561a 60%,#8a8f86)"></div>
    <h3>Electrical</h3>
    <p>BRTL carries out the design, installation, commissioning and maintenance of a wide range of electrical systems for clients.</p>
  </div>
</section>

<h2 class="sec-title serif" style="top:1439px"><span>&#9670;Our Projects&#9670;</span></h2>
<div class="tabs">
  <div class="tab all" style="left:412px;width:56px">All</div>
  <div class="tab" style="left:487px;width:151px">Current Projects</div>
  <div class="tab" style="left:654px;width:133px">Past Projects</div>
</div>

<article class="project" style="left:124px">
  <div class="pic" role="img" aria-label="Aerial render of a master-planned valley development" style="background:linear-gradient(180deg,#7fa873,#5b8e55);position:relative">
    <div style="position:absolute;left:17px;top:17px;width:266px;height:154px;background:rgba(10,133,191,.75);display:flex;align-items:center;justify-content:center">
      <svg width="34" height="34"><circle cx="14" cy="14" r="10" stroke="#fff" stroke-width="2.5" fill="none"/><path d="M14 9v10M9 14h10M21 21l9 9" stroke="#fff" stroke-width="2.5"/></svg>
    </div>
  </div>
  <h4>Harlow Vale Telecommunications Backhaul</h4>
  <p>The installation of Fibre optic back haul for Harlow Vale New development 'Vista' http://www.harlowvale.com.au/masterplan The installation of 4.0 kilometres of telecommunications pit and pipe infrastructure from Fernhill Road through</p>
</article>
<article class="project" style="left:451px">
  <div class="pic" role="img" aria-label="Render of twin residential towers with green facades" style="background:linear-gradient(180deg,#e4ecf2,#c3a987 60%,#8a7a5c)"></div>
  <h4>Meridian Park</h4>
  <p>Meridian Park occupies nearly six hectares of the southern CBD, defining the city's 'downtown'. Meridian Park is the willow-1.jpgvisionary redevelopment of the old Ashgrove Brewing Co site, bordered by Kelmore Road and Tandy Streets in Westbury.</p>
</article>
<article class="project" style="left:776px">
  <div class="pic" role="img" aria-label="Aerial render of a master-planned valley development" style="background:linear-gradient(180deg,#9cb98e,#6f9a63 50%,#a8b5a0)"></div>
  <h4>Harlow Vale Telecommunications Backhaul</h4>
  <p>The installation of Fibre optic back haul for Harlow Vale New development 'Vista' http://www.harlowvale.com.au/masterplan The installation of 4.0 kilometres of telecommunications pit and pipe infrastructure from Fernhill Road through</p>
</article>

<footer class="footer">
  <h5 class="serif" style="left:17px">Contact BRTL</h5>
  <div class="intro">Please contact us on 1300 555 214 or fill out below</div>
  <div class="field" style="left:17px;top:103px;width:142px;height:27px">First Name</div>
  <div class="field" style="left:164px;top:103px;width:136px;height:27px">Last Name</div>
  <div class="field" style="left:17px;top:135px;width:283px;height:26px">Email Address</div>
  <div class="field" style="left:17px;top:166px;width:283px;height:27px">Primary Contact Phone</div>
  <div class="field" style="left:17px;top:199px;width:283px;height:93px">How can we help you today?</div>
  <div class="submit">SUBMIT</div>

  <h5 class="serif" style="left:327px">My Account</h5>
  <div class="flist" style="left:327px">
    <div>My Account</div><div>Sign In</div><div>Order Status</div><div>My Cart</div><div>My Wishlist</div>
  </div>

  <h5 class="serif" style="left:490px">Information</h5>
  <div class="flist" style="left:490px;width:215px">
    <div>About Us</div><div>Services</div><div>ISP</div><div>Recent Projects</div><div>Contact Us</div><div>Blog</div>
  </div>

  <h5 class="serif" style="left:735px">Latest Tweets</h5>
  <div class="tweets">
    <div class="tweet"><i></i><p>Lumen has now a Stratus version - http://t.co/Xk4pLm92Qa<small>01:53 AM Dec 19th</small></p></div>
    <div class="tweet"><i></i><p>Lumen has now a Stratus version - http://t.co/Xk4pLm92Qa<small>01:53 AM Dec 19th</small></p></div>
    <div class="tweet"><i></i><p>Lumen has now a Stratus version - http://t.co/Xk4pLm92Qa<small>01:53 AM Dec 19th</small></p></div>
  </div>

  <div class="rule"></div>
  <div class="copy">Copyright 2015 BRTL Group. All Rights Reserved. Sitemap</div>
</footer>

</body>
</html>
```